Marigold Synchronized Swim Team's Clubhouse (web page)

Fun, Super Easy to read and navigate. Please error on the side of too large font sizes rather than too small font sizes.

We are a New Orleans (USA) based club for adults and youth of all genders.

We have youth and adult performance and competition teams. We teach synchronized swimming. We perform at special events.

Webpage should allow for

1. Sign up for classes, camps and teams (pay fees, sign waivers, reserve a spot and link to national Delmar Aquaform club membership website in order to buy required national membership).Make our multi step registration process easy, quick, pleasant.

2. Provide an area to upload practice schedules.
and performance calendar.

3. Easily
Hire one of our synchro squad to perform at special events.

4. Embedded Google Calndar

5 Members only site
( one away for youth and one area for adults. )

6 Show off our new logo, photos and videos. Be able to change these images often.

Our team colors are red, aqua and pink.

7. Buy logo gear

Click to team shop at
Brindle cove.com and other future team shops.

8. One click to become a sponsor of the team.

An area to show off sponsor logos. We will have several levels of sponsorships. It is important to have small medium and large logo spots. WE also will have a wall of names of folks who donate 10 - 100 dollars to sponsor the team.

We want the experience to be fun . We do not want headache producing events.

Our team colors are red, pink and aqua. WE have not settled on a specific red or pink yet. You are free to play around with different tones and hues. I tend toward a sholcking pink and cherry red. But really do want to see what your thoughts are for our reds and pinks. Also feel free to vary aqua from a light to dark. But we do want to stay away from navy.
Thanks for your hard work and creativity.

Target Market(s)

All ages, genders and ethnicity. Swimmers, dancers and event planners.

Coding

Coded - Design and coding required

Number of Pages Required

4 page

Font styles to use
Sans Serif

Colors
ec1f27
0293ce
f59195

Requirements
Must have
• See p descriptions +
• Fine #20 is our logo and
• Playful, bold, elegant, Colorful (red, aqua and pink are our team colors).
• I want to be able to plug in / update photos , schedules, release forms, almost everything as our seasons change. I do not know ( Newbury) do I want coded or incised site. All advice welcome.
Nice to have
• Your flare as a designer. Thank you for making us better through your creativity, ability to edit, clarify and advice. :-)
Should not have
• Confusion.

```html
<!DOCTYPE html>
<html lang="en">
<head>
<meta charset="utf-8">
<title>Tidewell LLC – Swimming Team Clubhouse</title>
<link href="https://fonts.googleapis.com/css2?family=Oswald:wght@500;600&family=Roboto:wght@400;500;700&display=swap" rel="stylesheet">
<style>
:root{
  --aqua:#0293ce;
  --red:#ec1f27;
  --pink:#f59195;
  --pink-edge:#e8767b;
  --tab:#8a5b5e;
  --ink:#333;
  --muted:#666;
  --cal-red:#e9573f;
  --orange:#f39c12;
  --dark:#1d1d1f;
  --band:#eeeeee;
}
*{box-sizing:border-box;margin:0;padding:0}
html,body{width:1200px;height:3495px;overflow:hidden}
body{font-family:"Roboto",Arial,sans-serif;color:var(--ink);background:#fff;position:relative}
.wrap{width:1000px;margin:0 auto;position:relative}
a{color:inherit;text-decoration:none}

/* header */
.topbar{position:absolute;top:0;right:0;width:790px;height:28px;background:var(--aqua);clip-path:polygon(26px 0,100% 0,100% 100%,0 100%);color:#fff;font-size:13px;display:flex;align-items:center;gap:34px;padding-left:210px}
.topbar .soc{display:flex;gap:6px}
.topbar .soc i{width:16px;height:16px;border-radius:50%;background:#fff;display:block}
.header{height:140px;position:relative}
.brand{position:absolute;left:98px;top:14px;display:flex;align-items:center;gap:10px}
.brand .mark{width:64px;height:64px;border-radius:50%;background:var(--aqua)}
.brand span{font-weight:700;font-size:22px;color:var(--aqua)}
.nav{position:absolute;right:95px;top:72px;display:flex;gap:30px;align-items:center;font-size:13px;color:#444}
.nav .signup{background:var(--red);color:#fff;padding:9px 16px;border-radius:3px}

/* hero */
.hero{position:relative;height:525px;overflow:hidden}
.hero .photo{position:absolute;inset:0;background:linear-gradient(160deg,#8a8f96 0%,#6d8ea0 40%,#3f9fb7 70%,#9ab0b8 100%)}
.hero h1{position:absolute;left:742px;top:205px;font-family:"Oswald",sans-serif;font-weight:600;font-size:48px;color:#fff;letter-spacing:1px}
.hero h2{position:absolute;left:742px;top:268px;font-family:"Oswald",sans-serif;font-weight:500;font-size:34px;color:#fff}
.hero .dots{position:absolute;left:745px;top:330px;display:flex;gap:8px}
.hero .dots i{width:12px;height:12px;border-radius:50%;background:#fff;display:block}
.hero .dots i:first-child{border:2px solid #fff;background:transparent}
.hero svg{position:absolute;left:0;bottom:0}

/* section titles */
.sec-title{text-align:center;font-size:30px;font-weight:500;color:#333;letter-spacing:.5px}
.lead{text-align:center;font-size:12px;color:var(--muted);line-height:1.7;width:700px;margin:16px auto 0}

/* how it works */
.how{padding-top:80px;height:1090px}
.how{height:auto}
.cards{display:flex;gap:24px;margin-top:60px;margin-left:7px}
.card{width:312px;height:291px;background:var(--pink);border:2px solid var(--pink-edge);position:relative;text-align:center;color:#fff}
.card svg{margin-top:28px}
.card h3{font-size:19px;font-weight:500;margin-top:14px}
.card p{font-size:12px;line-height:1.6;padding:4px 40px 0}
.card .more{position:absolute;bottom:-2px;left:50%;transform:translateX(-50%);background:var(--tab);font-size:12px;padding:10px 26px;clip-path:polygon(12px 0,calc(100% - 12px) 0,100% 100%,0 100%)}

/* calendar + events */
.agenda{display:flex;margin-top:86px;margin-left:7px;gap:24px}
.calendar{width:313px;height:310px;background:#fafafa;border:1px solid #e5e5e5;border-radius:4px;overflow:hidden}
.cal-head{background:var(--cal-red);color:#fff;height:50px;display:flex;align-items:center;justify-content:space-between;padding:0 22px;font-size:17px}
.cal-grid{display:grid;grid-template-columns:repeat(7,1fr);padding:12px 10px;row-gap:16px;text-align:center;font-size:13px}
.cal-grid .dn{font-size:9px;color:#888}
.cal-grid .dn.we{color:var(--orange)}
.cal-grid .off{color:#aaa}
.cal-grid .today{background:var(--orange);color:#fff;border-radius:50%;width:28px;height:28px;line-height:28px;margin:-6px auto}
.events{flex:1;position:relative}
.events h3{font-size:25px;font-weight:500;margin-top:2px}
.events .upload{position:absolute;right:0;top:-6px;background:#3a3a3a;color:#fff;font-size:15px;padding:9px 14px;border-radius:3px}
.ev-list{display:grid;grid-template-columns:1fr 1fr;gap:30px 20px;margin-top:28px}
.ev{display:flex;gap:14px}
.ev .img{width:130px;height:104px;flex:none;background:linear-gradient(135deg,#3fa8cf,#a8d7e6)}
.ev .img.b{background:linear-gradient(135deg,#c94a57,#e7b3a8)}
.ev h4{font-size:16px;font-weight:400}
.ev .date{color:var(--red);font-style:italic;font-size:14px;margin:8px 0 6px}
.ev p{font-size:12px;color:var(--muted);line-height:1.5}

/* welcome */
.welcome{position:absolute;top:1638px;left:0;width:1200px;height:475px;background:linear-gradient(120deg,#1f3f4e,#163040 60%,#2b4a58);color:#fff}
.welcome .video{position:absolute;left:114px;top:86px;width:430px;height:304px;border:4px solid #fff;background:linear-gradient(150deg,#49a6c6,#b34553 60%,#5e9eb8)}
.welcome .play{position:absolute;left:50%;top:50%;transform:translate(-50%,-50%)}
.welcome .text{position:absolute;left:582px;top:92px;width:508px}
.welcome h2{font-size:30px;font-weight:500;line-height:1.2}
.welcome p{font-size:12px;line-height:1.7;margin-top:14px;color:#dde}
.welcome .btn{display:inline-block;margin-top:34px;border:1px solid #fff;padding:10px 16px;font-size:13px}

/* members */
.members{position:absolute;top:2178px;left:0;width:1200px}
.members .lead{width:980px}
.mbtns{display:flex;justify-content:center;gap:12px;margin-top:24px}
.mbtns a{font-size:11px;font-weight:700;color:#fff;padding:11px 18px;border-radius:3px}
.mbtns .y{background:var(--aqua)}
.mbtns .a{background:var(--red)}
.mboxes{display:flex;gap:52px;width:920px;margin:110px auto 0}
.mbox{flex:1;height:210px;border:2px dashed var(--red);border-radius:3px;text-align:center;padding-top:36px;background:#fff}
.mbox h3{color:var(--red);font-size:20px;font-weight:500}
.mbox p{font-size:12px;line-height:1.6;color:var(--muted);padding:14px 60px 0}
.mbox .btn{display:inline-block;margin-top:14px;border:1px solid #666;font-size:11px;padding:7px 10px}

/* testimonials */
.testi{position:absolute;top:2661px;left:0;width:1200px;height:440px;background:var(--band)}
.testi .sec-title{margin-top:116px}
.quotes{display:flex;gap:60px;width:1000px;margin:44px auto 0}
.quote{flex:1;display:flex;gap:30px;position:relative}
.quote .face{width:122px;height:122px;border-radius:50%;flex:none;background:linear-gradient(160deg,#d94a5a,#cfa08c);border:4px solid #fff}
.quote p{font-style:italic;font-size:12px;line-height:1.6;color:var(--muted)}
.quote .who{color:var(--red);font-style:italic;font-size:14px;margin-top:18px}
.quote .mark{position:absolute;right:10px;bottom:-10px;font-size:70px;color:#555;font-family:Georgia,serif;line-height:1}

/* footer */
.footer{position:absolute;top:3099px;left:0;width:1200px;height:396px;background:var(--dark);color:#fff}
.footer .wave{position:absolute;top:-70px;left:0}
.fcols{position:absolute;top:88px;left:98px;width:1000px;height:200px}
.fcol{position:absolute;top:0}
.fcol h4{font-size:16px;font-weight:500;margin-bottom:18px}
.fcol p,.fcol li{font-size:13px;line-height:1.6}
.fcol ul{list-style:none}
.fcol li{margin-bottom:6px}
.fcol li::before{content:"›";margin-right:12px}
.ficon{display:flex;align-items:center;gap:16px;margin-top:12px;font-size:13px}
.news input{display:block;width:226px;height:40px;border:0;margin-top:16px;padding-left:10px;font-size:11px}
.news .btn{display:inline-block;margin-top:16px;background:var(--aqua);padding:12px 13px;font-size:12px;font-weight:500}
.social li::before{content:none}
.social li{display:flex;align-items:center;gap:10px;margin-bottom:10px}
.social i{width:24px;height:24px;border:1px solid #fff;border-radius:50%;display:block}
.copy{position:absolute;left:0;right:0;top:350px;text-align:center;font-size:12px;color:#ccc}
.copy::before{content:"";position:absolute;left:98px;right:98px;top:-22px;border-top:1px solid #333}
</style>
</head>
<body>

<div class="topbar">
  <span>&#9742; 555-014-7230</span>
  <span>&#9993; info@tidewell.com</span>
  <span class="soc"><i></i><i></i><i></i><i></i></span>
  <span>&#9906;</span>
</div>

<header class="header">
  <div class="brand"><div class="mark"></div><span>TIDEWELL</span></div>
  <nav class="nav">
    <a>HOME</a><a>ABOUT US</a><a>SERVICES</a><a>MEMBERS</a><a>BLOG</a><a>GALLERY</a><a>CONTACT</a><a class="signup">SIGN UP</a>
  </nav>
</header>

<section class="hero">
  <div class="photo" role="img" aria-label="Photo of swimmers performing a synchronized leg lift at a pool while spectators watch"></div>
  <h1>TIDEWELL LLC</h1>
  <h2>Swimming Team Clubhouse</h2>
  <div class="dots"><i></i><i></i><i></i><i></i></div>
  <svg width="1200" height="110" viewBox="0 0 1200 110" preserveAspectRatio="none">
    <path d="M0 70 Q600 -20 1200 60 L1200 110 L0 110Z" fill="#0293ce"/>
    <path d="M0 88 Q600 10 1200 78 L1200 110 L0 110Z" fill="#fff"/>
  </svg>
</section>

<section class="how wrap">
  <h2 class="sec-title">HOW IT WORKS</h2>
  <p class="lead">Sed ut perspiciatis unde omnis iste natus error sit voluptatem accusantium doloremque laudantium, totam rem aperiam, eaque ipsa quae ab illo inventore veritatis et quasi architecto beatae vitae dicta sunt explicabo.</p>
  <div class="cards">
    <div class="card">
      <svg width="110" height="100" viewBox="0 0 110 100"><path d="M55 92 L12 50 A24 24 0 0 1 55 18 A24 24 0 0 1 98 50 Z" fill="none" stroke="#fff" stroke-width="7" stroke-linejoin="round"/><rect x="40" y="40" width="30" height="20" rx="2" fill="#fff"/><circle cx="55" cy="50" r="5" fill="#f59195"/></svg>
      <h3>PAY FEES</h3>
      <p>Sed ut perspiciatis unde omnis iste natus error sit voluptatem accusantium doloremque laudantium, totam rem aperiam</p>
      <a class="more">READ MORE &#9656;</a>
    </div>
    <div class="card">
      <svg width="110" height="100" viewBox="0 0 110 100"><path d="M55 92 L12 50 A24 24 0 0 1 55 18 A24 24 0 0 1 98 50 Z" fill="none" stroke="#fff" stroke-width="7" stroke-linejoin="round"/><circle cx="55" cy="42" r="7" fill="#fff"/><path d="M42 62 Q55 46 68 62Z" fill="#fff"/></svg>
      <h3>SIGN WAIVERS</h3>
      <p>Sed ut perspiciatis unde omnis iste natus error sit voluptatem accusantium doloremque laudantium, totam rem aperiam</p>
      <a class="more">READ MORE &#9656;</a>
    </div>
    <div class="card">
      <svg width="110" height="100" viewBox="0 0 110 100"><path d="M55 92 L12 50 A24 24 0 0 1 55 18 A24 24 0 0 1 98 50 Z" fill="none" stroke="#fff" stroke-width="7" stroke-linejoin="round"/><rect x="42" y="38" width="26" height="17" fill="none" stroke="#fff" stroke-width="3"/><rect x="37" y="57" width="36" height="4" fill="#fff"/></svg>
      <h3>RESERVE A SPOT</h3>
      <p>Sed ut perspiciatis unde omnis iste natus error sit voluptatem accusantium doloremque laudantium, totam rem aperiam</p>
      <a class="more">READ MORE &#9656;</a>
    </div>
  </div>

  <div class="agenda">
    <div class="calendar">
      <div class="cal-head"><span>&#8249;</span><span>November 2015</span><span>&#8250;</span></div>
      <div class="cal-grid">
        <span class="dn">MON</span><span class="dn">TUE</span><span class="dn">WED</span><span class="dn">THU</span><span class="dn">FRI</span><span class="dn we">SAT</span><span class="dn we">SUN</span>
        <span class="off">30</span><span>1</span><span>2</span><span>3</span><span>4</span><span>5</span><span>6</span>
        <span>7</span><span>8</span><span>9</span><span>10</span><span>11</span><span>12</span><span>13</span>
        <span>14</span><span>15</span><span>16</span><span>17</span><span class="today">18</span><span>19</span><span>20</span>
        <span>21</span><span>22</span><span>23</span><span>24</span><span>25</span><span>26</span><span>27</span>
        <span>28</span><span>29</span><span>30</span><span class="off">1</span><span class="off">2</span><span class="off">3</span><span class="off">4</span>
      </div>
    </div>
    <div class="events">
      <h3>SPECIAL EVENTS</h3>
      <a class="upload">Upload Schedules</a>
      <div class="ev-list">
        <div class="ev"><div class="img" role="img" aria-label="Swimmers racing in a pool"></div><div><h4>Lorem ipsum dolor sit</h4><p class="date">02 - JAN - 2017</p><p>Lorem ipsum dolor sit amet, consectetur adipiscing elit. Sed blandit massa</p></div></div>
        <div class="ev"><div class="img b" role="img" aria-label="Team members in red swim caps"></div><div><h4>Lorem ipsum dolor sit</h4><p class="date">02 - JAN - 2017</p><p>Lorem ipsum dolor sit amet, consectetur adipiscing elit. Sed blandit massa</p></div></div>
        <div class="ev"><div class="img" role="img" aria-label="Swimmer training at the pool edge"></div><div><h4>Lorem ipsum dolor sit</h4><p class="date">02 - JAN - 2017</p><p>Lorem ipsum dolor sit amet, consectetur adipiscing elit. Sed blandit massa</p></div></div>
        <div class="ev"><div class="img b" role="img" aria-label="Young swimmers posing together"></div><div><h4>Lorem ipsum dolor sit</h4><p class="date">02 - JAN - 2017</p><p>Lorem ipsum dolor sit amet, consectetur adipiscing elit. Sed blandit massa</p></div></div>
      </div>
    </div>
  </div>
</section>

<section class="welcome" role="region" aria-label="Welcome">
  <div class="video" role="img" aria-label="Video still of the team in red caps forming a circle in the pool">
    <svg class="play" width="58" height="42" viewBox="0 0 58 42"><rect width="58" height="42" rx="10" fill="#fff"/><path d="M23 12 L38 21 L23 30Z" fill="#222"/></svg>
  </div>
  <div class="text">
    <h2>WELCOME TO<br>TIDEWELL LLC</h2>
    <p>Sed ut perspiciatis unde omnis iste natus error sit voluptatem accusantium doloremque laudantium, totam rem aperiam, eaque ipsa quae ab illo inventore veritatis et quasi architecto beatae vitae dicta sunt explicabo. Nemo enim ipsam voluptatem quia voluptas sit aspernatur aut odit aut fugit, sed quia consequuntur magni dolores eos qui ratione voluptatem.</p>
    <p>Lorem ipsum dolor sit amet, consectetur adipiscing elit, sed do eiusmod tempor incididunt ut labore et dolore magna aliqua. Ut enim ad minim veniam, quis nostrud exercitation ullamco laboris nisi ut aliquip ex ea commodo consequat. Duis aute irure dolor</p>
    <a class="btn">READ MORE</a>
  </div>
</section>

<section class="members">
  <h2 class="sec-title">MEMBERS ONLY</h2>
  <p class="lead">Lorem ipsum dolor sit amet, consectetur adipiscing elit, sed do eiusmod tempor incididunt ut labore et dolore magna aliqua. Ut enim ad minim veniam, quis nostrud exercitation ullamco laboris nisi ut aliquip ex ea commodo consequat. Duis aute irure dolor in reprehenderit in voluptate velit esse cillum dolore eu fugiat nulla pariatur. Excepteur sint occaecat cupidatat non proident, sunt in culpa qui officia deserunt mollit anim id est laborum</p>
  <div class="mbtns"><a class="y">ONE AWAY FOR YOUTH &#9656;</a><a class="a">ONE AREA FOR ADULTS &#9656;</a></div>
  <div class="mboxes">
    <div class="mbox"><h3>TEAM SHOPS</h3><p>Lorem ipsum dolor sit amet, consectetur adipiscing elit, sed do eiusmod tempor incididunt ut labore et dolore magna aliqua. Ut enim ad minim veniam, quis nostrud exercitation</p><a class="btn">TEAM SHOPS &#9656;</a></div>
    <div class="mbox"><h3>SPONSOR</h3><p>Lorem ipsum dolor sit amet, consectetur adipiscing elit, sed do eiusmod tempor incididunt ut labore et dolore magna aliqua. Ut enim ad minim veniam, quis nostrud exercitation</p><a class="btn">READ MORE &#9656;</a></div>
  </div>
</section>

<section class="testi">
  <h2 class="sec-title">TESTIMONIALS</h2>
  <div class="quotes">
    <div class="quote"><div class="face" role="img" aria-label="Portrait of a team swimmer in a red cap"></div><div><p>“ Nemo enim ipsam voluptatem quia voluptas sit aspernatur aut odit aut fugit, sed quia consequuntur magni dolores eos qui ratione voluptatem sequi nesciunt.</p><p class="who">John Doe -<br>Tidewell llc</p></div><span class="mark">”</span></div>
    <div class="quote"><div class="face" role="img" aria-label="Portrait of a young team member"></div><div><p>“ Nemo enim ipsam voluptatem quia voluptas sit aspernatur aut odit aut fugit, sed quia consequuntur magni dolores eos qui ratione voluptatem sequi nesciunt.</p><p class="who">John Doe -<br>Tidewell llc</p></div><span class="mark">”</span></div>
  </div>
</section>

<footer class="footer">
  <svg class="wave" width="1200" height="80" viewBox="0 0 1200 80" preserveAspectRatio="none">
    <path d="M0 40 Q600 -10 1200 30 L1200 80 L0 80Z" fill="#0293ce"/>
    <path d="M0 58 Q600 10 1200 50 L1200 80 L0 80Z" fill="#fff"/>
    <path d="M0 70 Q600 30 1200 62 L1200 80 L0 80Z" fill="#1d1d1f"/>
  </svg>
  <div class="fcols">
    <div class="fcol" style="left:0">
      <h4>CONTACT US</h4>
      <p>Tidewell llc<br>12 Harbor Lane Avondale, LA 70094 USA</p>
      <div class="ficon"><svg width="18" height="18" viewBox="0 0 24 24"><path d="M6 2 L10 6 L8 9 Q10 14 15 16 L18 14 L22 18 L19 22 Q8 21 2 6Z" fill="none" stroke="#fff" stroke-width="1.6"/></svg>Call Us 555.347.4000</div>
      <div class="ficon"><svg width="18" height="14" viewBox="0 0 18 14"><rect x="1" y="1" width="16" height="12" fill="none" stroke="#fff" stroke-width="1.4"/><path d="M1 1 L9 8 L17 1" fill="none" stroke="#fff" stroke-width="1.4"/></svg>info@tidewellclub.com</div>
    </div>
    <div class="fcol" style="left:345px">
      <h4>QUICK LINKS</h4>
      <ul><li>Home</li><li>About us</li><li>Services</li><li>Blog</li><li>Publications</li><li>Contact us</li></ul>
    </div>
    <div class="fcol news" style="left:566px">
      <h4>SIGN UP FOR NEWSLETTER</h4>
      <p style="font-size:12px;width:230px">Excepteur sint occaecat cupidatat non proident, sunt in culpa qui</p>
      <input type="text" placeholder="Enter Name">
      <a class="btn">SUBSCRIBE</a>
    </div>
    <div class="fcol social" style="left:904px">
      <h4>SOCIAL</h4>
      <ul><li><i></i>Poolside</li><li><i></i>Splashfeed</li><li><i></i>Ripplenet</li><li><i></i>Wavecast</li></ul>
    </div>
  </div>
  <p class="copy">2016 © Copyrights Tidewell llc.All Rights Reserved</p>
</footer>

</body>
</html>
```